Health and Wellness company needs flyer to promote free seminar

Corvella Motion studio is a health and wellness company that offers an exercise program designed by physical therapists to help relieve pain and improve mobility. Our business is a new concept that is not well understood by the public. In order to promote our business we offer a free seminar where we present information regarding the underlying cause of pain and tightness. During the seminar we also perform a posture screen and movement testing for all participants.

Target Market(s)

Mostly healthy and active women ages 25-65

Industry/Entity Type

Health And Wellness

Font styles to use
Sans Serif

Colors

Designer to choose colors to be used in the design.

Requirements
Must have
• Title: Eliminate Pain and Tightness For Good
• Paragraph: Corvella Motion Studio offers a free 60 minute seminar: "The Busy Walker's Manual for Stretching and Living Lighter."
• What to Expect:
• • Identify the underlying cause of your pain and mobility issues
• • Expose what gets in the way of you moving and feeling better
• • Learn why traditional exercises don’t help and can actually make the problem worse
• • Reveal what your posture is saying and how that impacts you
• • Experience your muscle imbalances through movement tests
• • Discover the training method that realigns your posture, increases your mobility and reduces your pain
• Call to action: RSVP online at corvellamotionstudio.com
Nice to have
• Use a relevant image showing a female dealing with tightness in the low back, legs, etc.
• Emphasize that the seminar is FREE.
• Make the call to action prominent.

```html
<!DOCTYPE html>
<html lang="en">
<head>
<meta charset="utf-8">
<title>Corvella Motion Studio – Free Seminar Flyer</title>
<link rel="stylesheet" href="https://fonts.googleapis.com/css2?family=Roboto+Condensed:wght@700&family=Open+Sans:wght@600;700&family=Arimo:wght@700&display=swap">
<style>
  :root {
    --purple: #5b5aa8;
    --orange: #f7941d;
    --ink: #1f1f1f;
    --page: #ffffff;
    --backdrop: #e9e9ec;
    --band-top: #ececec;
    --band-bottom: #c8c8c8;
  }
  * { box-sizing: border-box; margin: 0; padding: 0; }
  html, body { width: 1020px; height: 1200px; overflow: hidden; background: var(--backdrop); }
  .flyer {
    position: absolute; left: 99px; top: 20px;
    width: 821px; height: 1160px;
    background: var(--page); overflow: hidden;
    box-shadow: 0 4px 14px rgba(0,0,0,.18);
  }
  .headline-bar {
    position: absolute; left: 320px; top: 0; width: 501px; height: 99px;
    background: var(--purple);
    clip-path: polygon(0 0, 100% 0, 100% 100%, 7% 100%);
    display: flex; align-items: center; justify-content: flex-end; padding-right: 20px;
    font: 700 24px "Roboto Condensed", sans-serif; color: #fff; letter-spacing: .2px;
  }
  .hero-photo {
    position: absolute; left: 0; top: 99px; width: 821px; height: 420px;
    background: linear-gradient(120deg, #3e4048 0%, #7b808c 35%, #b9bcc4 55%, #6f7790 75%, #2f3340 100%);
  }
  .brand-panel {
    position: absolute; left: 0; top: 0; width: 345px; height: 121px;
    background: var(--page);
    clip-path: polygon(0 0, 100% 0, 92% 100%, 0 100%);
    display: flex; align-items: center; gap: 12px; padding-left: 18px;
  }
  .brand-mark { width: 30px; height: 30px; background: var(--orange); flex: none; }
  .brand-name { font: 700 22px "Open Sans", sans-serif; color: var(--purple); white-space: nowrap; }
  .title-band {
    position: absolute; left: 0; top: 519px; width: 821px; height: 138px;
    background: linear-gradient(180deg, var(--band-top), var(--band-bottom));
    text-align: center; padding-top: 14px;
  }
  .title-band h1 {
    font: 700 38px/44px "Roboto Condensed", sans-serif; color: var(--purple); text-transform: uppercase;
  }
  .title-band p {
    margin-top: 6px; font: 700 18px "Open Sans", sans-serif; color: var(--ink); text-transform: uppercase;
  }
  .expect-bar { position: absolute; left: 0; top: 664px; width: 480px; height: 62px; }
  .expect-label {
    position: absolute; left: 0; top: 0; width: 386px; height: 62px;
    background: var(--purple); clip-path: polygon(0 0, 100% 0, 93% 100%, 0 100%);
    font: 700 42px/62px "Roboto Condensed", sans-serif; color: #fff; padding-left: 50px;
  }
  .expect-stripes { position: absolute; left: 388px; top: 0; }
  .expect-list {
    position: absolute; left: 22px; top: 735px; width: 790px; list-style: none;
    font: 700 16.5px/22px "Open Sans", sans-serif; color: var(--ink);
  }
  .expect-list li { position: relative; padding-left: 26px; margin-bottom: 23px; }
  .expect-list li::before {
    content: ""; position: absolute; left: 4px; top: 8px; width: 7px; height: 7px;
    border-radius: 50%; background: var(--orange);
  }
  .signup {
    position: absolute; left: 0; top: 995px; width: 821px; text-align: center;
    font: 700 32px "Arimo", sans-serif; color: var(--purple);
  }
  .signup .free { color: var(--orange); }
  .rsvp {
    position: absolute; left: 140px; top: 1044px; width: 541px; height: 44px;
    background: var(--orange); clip-path: polygon(4% 0, 100% 0, 96% 100%, 0 100%);
    font: 700 21px/44px "Arimo", sans-serif; color: #fff; text-align: center;
    white-space: nowrap;
  }
  .studio {
    position: absolute; top: 1102px; height: 58px; color: #fff; text-align: center;
  }
  .studio-houston { left: 0; width: 445px; background: var(--purple); clip-path: polygon(0 0, 100% 0, 95% 100%, 0 100%); padding-right: 30px; }
  .studio-portland { left: 425px; width: 396px; background: var(--orange); clip-path: polygon(5% 0, 100% 0, 100% 100%, 0 100%); padding-left: 30px; }
  .studio-city { display: block; font: 700 16px/20px "Arimo", sans-serif; padding-top: 6px; }
  .studio-phone { display: block; font: 700 24px/28px "Roboto Condensed", sans-serif; }
</style>
</head>
<body>
  <main class="flyer">
    <div class="hero-photo" role="img" aria-label="Woman in a blue sports top holding a barbell across her shoulders in a gym"></div>
    <div class="brand-panel">
      <span class="brand-mark"></span>
      <span class="brand-name">Corvella Motion studio</span>
    </div>
    <div class="headline-bar">ELIMINATE PAIN AND TIGHTNESS FOR GOOD</div>

    <section class="title-band">
      <h1>Corvella Motion Studio<br>Offers a Free 60 Minute Seminar</h1>
      <p>The Busy Walker's Manual for Stretching and Living Lighter</p>
    </section>

    <div class="expect-bar">
      <div class="expect-label">What to Expect</div>
      <svg class="expect-stripes" width="92" height="62" viewBox="0 0 92 62">
        <polygon points="18,0 34,0 16,62 0,62" fill="#f7941d"/>
        <polygon points="46,0 62,0 44,62 28,62" fill="#f7941d"/>
        <polygon points="74,0 90,0 72,62 56,62" fill="#f7941d"/>
      </svg>
    </div>

    <ul class="expect-list">
      <li>Identify the underlying cause of your pain and mobility issues</li>
      <li>Expose what gets in the way of you moving and feeling better</li>
      <li>Learn why traditional exercises don’t help and can actually make the problem worse<br>Reveal what your posture is saying and how that impacts you</li>
      <li>Experience your muscle imbalances through movement tests</li>
      <li>Discover the training method that realigns your posture, increases your mobility and reduces your pain</li>
    </ul>

    <p class="signup">Sign up for the <span class="free">FREE</span> seminar today</p>
    <div class="rsvp">RSVP online at corvellamotionstudio.com</div>

    <div class="studio studio-houston">
      <span class="studio-city">Studio Houston</span>
      <span class="studio-phone">CALL NOW:(281) 555-0147</span>
    </div>
    <div class="studio studio-portland">
      <span class="studio-city">Studio Portland</span>
      <span class="studio-phone">CALL NOW:(503) 555-0193</span>
    </div>
  </main>
</body>
</html>
```